Promotional business a5 Notepad design

I am looking for a custom a5 notepad design as a promotional item to give away to customers etc.
Attached will be a desk planner we had designed feel free to use as a reference.
We want the notepad to have lines running horizontal not squares like the desk planner example.

Industry/Entity Type

Hydraulic / industrial

Colors

Designer to choose colors to be used in the design.

```html
<!DOCTYPE html>
<html lang="en">
<head>
<meta charset="utf-8">
<title>Northline Hose &amp; Fittings – A5 Notepad</title>
<link href="https://fonts.googleapis.com/css2?family=Poppins:wght@400;600;700&display=swap" rel="stylesheet">
<style>
  :root {
    --brand-blue: #1530bf;
    --ink: #111111;
    --text-grey: #4a4a4a;
    --paper: #ffffff;
    --backdrop: #e9eaeb;
  }
  * { box-sizing: border-box; margin: 0; padding: 0; }
  html, body {
    width: 973px; height: 1200px; overflow: hidden;
    background: var(--backdrop);
    font-family: "Poppins", Arial, sans-serif;
  }
  .notepad {
    position: absolute; left: 76px; top: 20px;
    width: 821px; height: 1160px;
    background: var(--paper);
    border: 17px solid var(--brand-blue);
  }
  .brand {
    position: absolute; top: 52px; left: 0; right: 0;
    display: flex; align-items: center; justify-content: center; gap: 14px;
  }
  .brand-mark {
    width: 62px; height: 62px; border-radius: 50%;
    background: var(--ink);
  }
  .brand-name {
    font-weight: 700; font-size: 30px; letter-spacing: 1px;
    color: var(--brand-blue); text-transform: uppercase; line-height: 1;
  }
  .writing-lines { position: absolute; left: 50px; right: 50px; top: 198px; }
  .writing-line {
    height: 61px; border-bottom: 1.5px solid var(--ink);
  }
  .contact {
    position: absolute; left: 50px; right: 41px; top: 1061px;
    display: flex; justify-content: space-between; align-items: flex-end;
    font-size: 13.6px; line-height: 17px; color: var(--text-grey);
  }
  .contact-address { width: 240px; }
  .contact-direct { flex: 1; }
  .contact-web { color: var(--brand-blue); font-weight: 600; }
</style>
</head>
<body>
  <main class="notepad">
    <header class="brand">
      <span class="brand-mark"></span>
      <span class="brand-name">Northline Hose &amp; Fittings</span>
    </header>

    <section class="writing-lines">
      <div class="writing-line"></div><div class="writing-line"></div>
      <div class="writing-line"></div><div class="writing-line"></div>
      <div class="writing-line"></div><div class="writing-line"></div>
      <div class="writing-line"></div><div class="writing-line"></div>
      <div class="writing-line"></div><div class="writing-line"></div>
      <div class="writing-line"></div><div class="writing-line"></div>
      <div class="writing-line"></div><div class="writing-line"></div>
    </section>

    <footer class="contact">
      <p class="contact-address">2140 Harbor Ridge Road<br>Anchorage, Alaska 99501</p>
      <p class="contact-direct">Phone : 555-014-2287<br>name@northlinehose.com</p>
      <p class="contact-web">www.northlinehose.com</p>
    </footer>
  </main>
</body>
</html>
```